Business Card Design

We are a manufacturing and distribution company with most of our customer base being supermarkets. We have established brand guidelines that are attached.

```html
<!DOCTYPE html>
<html lang="en">
<head>
<meta charset="utf-8">
<title>Kelvora Business Card</title>
<link rel="stylesheet" href="https://fonts.googleapis.com/css2?family=Poppins:wght@400;500;700&display=swap">
<style>
  :root {
    --stage: #2a2523;
    --card: #1b1b1c;
    --red: #e41c26;
    --blue: #0a6ab3;
    --ink: #f2f2f2;
    --band: 12px;
  }
  * { margin: 0; padding: 0; box-sizing: border-box; }
  html, body { width: 1200px; height: 842px; overflow: hidden; }
  body {
    background: var(--stage);
    font-family: "Poppins", sans-serif;
    position: relative;
  }
  .card {
    position: absolute;
    top: 271px;
    width: 520px;
    height: 300px;
    background: var(--card);
    overflow: hidden;
    box-shadow: 0 10px 28px rgba(0,0,0,0.45);
  }
  .card--back { left: 50px; }
  .card--front { left: 630px; }

  .band {
    position: absolute;
    left: 0;
    width: 100%;
    height: var(--band);
    display: flex;
  }
  .band--top { top: 0; }
  .band--bottom { bottom: 0; }
  .band__red { background: var(--red); }
  .band__blue { background: var(--blue); flex: 1; }
  .band--top .band__red { width: 54%; }
  .band--bottom .band__red { width: 44%; }

  .contact {
    position: absolute;
    left: 150px;
    top: 62px;
    color: var(--ink);
    font-size: 13px;
    line-height: 1.3;
    letter-spacing: 0.04em;
    text-transform: uppercase;
  }
  .contact__name {
    font-weight: 700;
    font-size: 20px;
    letter-spacing: 0.03em;
    line-height: 1.1;
  }
  .contact__first { color: var(--red); }
  .contact__last { color: var(--blue); }
  .contact__role { font-size: 12px; margin-left: 18px; }
  .contact__rule {
    width: 56px;
    height: 1.5px;
    background: var(--red);
    margin: 10px 0 10px 78px;
  }
  .contact__phone { font-size: 15px; margin-left: 40px; }
  .contact__line { margin-left: 22px; }
  .contact__address { margin-left: 30px; }

  .brand {
    position: absolute;
    left: 0; right: 0;
    top: 104px;
    display: flex;
    align-items: center;
    justify-content: center;
    gap: 16px;
  }
  .brand__mark {
    width: 34px; height: 34px;
    background: var(--blue);
  }
  .brand__name {
    color: #ffffff;
    font-weight: 700;
    font-size: 48px;
    letter-spacing: 0.06em;
  }
</style>
</head>
<body>
  <section class="card card--back" aria-label="Business card, contact side">
    <div class="band band--top"><span class="band__red"></span><span class="band__blue"></span></div>
    <div class="contact">
      <p class="contact__name"><span class="contact__first">Marcus</span> <span class="contact__last">Delaney</span></p>
      <p class="contact__role">Managing Director</p>
      <div class="contact__rule"></div>
      <p class="contact__phone">044-987 654 321</p>
      <p class="contact__line">hello@kelvora.com</p>
      <p class="contact__line">www.kelvora.com</p>
      <div class="contact__rule"></div>
      <p class="contact__address">18, Harbour Mill Road</p>
      <p class="contact__address">30817, Northland</p>
    </div>
    <div class="band band--bottom"><span class="band__red"></span><span class="band__blue"></span></div>
  </section>

  <section class="card card--front" aria-label="Business card, brand side">
    <div class="band band--top"><span class="band__red"></span><span class="band__blue"></span></div>
    <div class="brand">
      <span class="brand__mark"></span>
      <span class="brand__name">KELVORA</span>
    </div>
    <div class="band band--bottom"><span class="band__red"></span><span class="band__blue"></span></div>
  </section>
</body>
</html>
```